Coffee House With Cycling Theme Wants Business Cards

We want to create a business card for a coffee house that has a cycling theme. We expect to use the current logo on one side of the business card and we have been considering adding the words 'COFFEE HOUSE' underneath (see example). For the other side of the business card we want an interesting design with tag-line, address and social media links (the normal business card stuff). See examples provided but we are not fixed on having it exactly as shown, we are very open to great creative ideas. Please note our logo has the initials ‘KR' in orange embedded in the design and this must be retained. However, you can play with the words COFFEE HOUSE as well as use the orange color on the backside of the business card, as you see fit. For an image on the backside of the business card it can be a photo, hand-drawn or whatever but it must visually combine coffee and cycling in some way. The interior of the Coffee House will be reclaimed wood, rustic and have an urban feel to it with cycling artifacts hanging from the walls/ceiling, etc. Finally, it would be beneficial if the business card design elements can be easily used on flyers and other promotional assets. Good luck, we are looking forward to seeing your creative ideas.

Target Market(s)

Coffee lovers and cycling fans

Contact Information for Business Card

See project description.

Colors

Designer to choose colors to be used in the design.

Requirements
Must have
• Must use the current logo provided and combine a coffee and bike theme.
Nice to have
• Orange is used in current logo and could be used as an accent color on the backside of the business card.

```html
<!DOCTYPE html>
<html lang="en">
<head>
<meta charset="utf-8">
<title>KR Coffee House – Business Cards</title>
<link rel="stylesheet" href="https://fonts.googleapis.com/css2?family=Open+Sans:wght@400;600;700&display=swap">
<style>
  :root {
    --orange: #f26a2e;
    --ink: #2b2b2b;
    --grey-dark: #3d3d3d;
    --paper: #ffffff;
    --backdrop: #b9b9b9;
  }
  * { margin: 0; padding: 0; box-sizing: border-box; }
  html, body { width: 1200px; height: 930px; overflow: hidden; }
  body {
    background: var(--backdrop);
    font-family: "Open Sans", sans-serif;
    position: relative;
  }
  .card {
    position: absolute;
    width: 560px;
    height: 320px;
    border-radius: 22px;
    overflow: hidden;
  }
  .card--front { left: 80px; top: 110px; background: var(--orange); }
  .card--back { left: 560px; top: 500px; background: var(--paper); }

  .wordmark {
    font-weight: 600;
    letter-spacing: 1px;
    line-height: 1.05;
    text-transform: uppercase;
  }
  .card--front .wordmark {
    position: absolute;
    left: 0; right: 0; top: 100px;
    text-align: center;
    color: var(--paper);
  }
  .wordmark__initials { display: block; font-size: 68px; }
  .wordmark__words { display: block; font-size: 38px; }

  .card--back .wordmark {
    position: absolute;
    right: 40px; top: 18px;
    text-align: center;
    color: var(--ink);
  }
  .card--back .wordmark__initials { font-size: 46px; }
  .card--back .wordmark__words { font-size: 25px; }

  .back-art { position: absolute; inset: 0; }

  .holder { position: absolute; left: 40px; top: 80px; }
  .holder__name {
    color: var(--orange);
    font-weight: 600;
    font-size: 21px;
    line-height: 28px;
    letter-spacing: 0.5px;
    text-transform: uppercase;
  }
  .holder__role { font-size: 12.5px; line-height: 16px; color: var(--ink); margin-top: 8px; }

  .contact { position: absolute; left: 40px; top: 156px; font-size: 13px; color: var(--ink); line-height: 19px; }
  .contact__address { margin-bottom: 6px; }
  .contact__row { display: flex; align-items: center; gap: 8px; }
  .contact__row svg { width: 10px; height: 10px; flex: none; }

  .social { position: absolute; right: 30px; top: 126px; font-size: 13px; color: var(--ink); line-height: 19px; }
  .social__row { display: flex; align-items: center; gap: 8px; margin-bottom: 6px; }
  .social__mark { width: 14px; height: 14px; border-radius: 3px; background: var(--orange); flex: none; }
</style>
</head>
<body>

<section class="card card--front" aria-label="Card front">
  <div class="wordmark">
    <span class="wordmark__initials">KR</span>
    <span class="wordmark__words">Coffee House</span>
  </div>
</section>

<section class="card card--back" aria-label="Card back">
  <svg class="back-art" viewBox="0 0 560 320" aria-hidden="true">
    <line x1="40" y1="114" x2="530" y2="114" stroke="#f26a2e" stroke-width="1.5"/>
    <line x1="40" y1="146" x2="250" y2="146" stroke="#f26a2e" stroke-width="1.5"/>
    <polygon points="230,320 380,294 380,320" fill="#3d3d3d"/>
    <polygon points="392,240 560,210 560,320 380,320" fill="#f26a2e"/>
  </svg>

  <div class="wordmark">
    <span class="wordmark__initials">KR</span>
    <span class="wordmark__words">Coffee House</span>
  </div>

  <div class="social">
    <div class="social__row"><span class="social__mark"></span>krcoffeehouse.com</div>
    <div class="social__row"><span class="social__mark"></span>krcoffeehouse.com</div>
  </div>

  <div class="holder">
    <div class="holder__name">Daniel Harper</div>
    <div class="holder__role">Director</div>
  </div>

  <div class="contact">
    <div class="contact__address">214b Harbour Lane,<br>Riverton, NZ, 8042</div>
    <div class="contact__row">
      <svg viewBox="0 0 10 10"><path d="M2 1 L4 1 L4.5 3 L3.3 3.8 Q4.5 6 6.2 6.7 L7 5.5 L9 6 L9 8 Q5 9.5 1 2 Z" fill="#f26a2e"/></svg>
      (555) 210-4837
    </div>
    <div class="contact__row">
      <svg viewBox="0 0 10 10"><rect x="0.5" y="2" width="9" height="6" fill="none" stroke="#f26a2e"/><path d="M0.5 2 L5 5.5 L9.5 2" fill="none" stroke="#f26a2e"/></svg>
      info@krcoffeehouse.com
    </div>
    <div class="contact__row">
      <svg viewBox="0 0 10 10"><circle cx="5" cy="5" r="4.3" fill="none" stroke="#f26a2e"/><ellipse cx="5" cy="5" rx="1.8" ry="4.3" fill="none" stroke="#f26a2e"/><line x1="0.7" y1="5" x2="9.3" y2="5" stroke="#f26a2e"/></svg>
      www.krcoffeehouse.com
    </div>
  </div>
</section>

</body>
</html>
```